New retail box design

We are looking at changing our packaging for retilers. I have templates of boxes and like a great design for new packaging.

I will attach pictures of our current packaging.

Industry/Entity Type

Ammunition manufacturing

Requirements
Must have
• warning label and company name

```html
<!DOCTYPE html>
<html lang="en">
<head>
<meta charset="utf-8">
<title>Liberty Range Ammo – 9mm Retail Box</title>
<link rel="stylesheet" href="https://fonts.googleapis.com/css2?family=Fira+Sans+Condensed:wght@400;600&family=Rubik:wght@800&display=swap">
<style>
  :root {
    --navy: #1b3553;
    --flag-blue: #2b5a80;
    --flag-red: #b0443d;
    --flag-white: #f0efed;
    --warn-red: #b0362f;
    --ink: #25282c;
    --page: #e6e4e0;
    --label-bg: #f7f6f4;
    --brass: #c9a24a;
    --copper: #b87443;
    --steel: #9ea3a8;
  }
  * { box-sizing: border-box; margin: 0; padding: 0; }
  html, body { width: 1200px; height: 800px; overflow: hidden; background: var(--page); }
  .dieline {
    position: absolute; left: 60px; top: 110px;
    display: flex; height: 580px;
    box-shadow: 0 6px 24px rgba(0,0,0,.12);
  }
  .panel { position: relative; overflow: hidden; height: 100%; }
  .panel + .panel { border-left: 1px dashed rgba(0,0,0,.18); }
  .panel--side { width: 300px; }
  .panel--front { width: 480px; }

  .flag-backdrop { position: absolute; inset: 0; }
  .panel--warnings .flag-backdrop {
    background: linear-gradient(180deg, var(--flag-blue) 0%, var(--flag-white) 35%, var(--flag-white) 45%, var(--flag-red) 70%, var(--flag-red) 100%);
  }
  .panel--front .flag-backdrop {
    background: linear-gradient(170deg, var(--flag-blue) 0%, var(--flag-white) 22%, var(--flag-white) 55%, var(--flag-red) 75%, var(--flag-red) 100%);
  }
  .panel--lead .flag-backdrop {
    background: linear-gradient(180deg, var(--flag-white) 0%, var(--flag-red) 30%, var(--flag-white) 55%, var(--flag-red) 80%, var(--flag-white) 100%);
  }

  .copy-card {
    position: absolute; inset: 26px 18px 26px 18px;
    background: rgba(255,255,255,.62); border-radius: 22px;
    padding: 22px 20px;
    font-family: "Fira Sans Condensed", sans-serif;
    color: var(--ink); font-size: 15px; line-height: 1.32;
  }
  .copy-card h2 {
    font-family: "Fira Sans Condensed", sans-serif;
    color: var(--warn-red); font-weight: 600; font-size: 22px; line-height: 1.1;
  }
  .copy-card .keep-away { font-weight: 600; font-size: 14px; margin: 6px 0 14px; text-transform: uppercase; }
  .copy-card .rules-title { font-weight: 600; font-size: 14px; text-transform: uppercase; margin-bottom: 6px; }
  .safety-rules { padding-left: 18px; }
  .safety-rules li { margin-bottom: 3px; }
  .lead-copy p { margin-bottom: 14px; }
  .lead-copy strong { color: var(--warn-red); font-weight: 600; text-transform: uppercase; }

  .brand-name {
    position: absolute; left: 34px; top: 54px;
    font-family: "Rubik", sans-serif; font-weight: 800; color: var(--navy);
    font-size: 72px; line-height: 1.0;
    text-transform: uppercase; letter-spacing: 1px;
  }
  .brand-name .brand-suffix { font-size: 24px; letter-spacing: 0; text-transform: none; }

  .art-cartridge {
    position: absolute; left: 44px; top: 330px; width: 84px; height: 210px;
    background: linear-gradient(180deg, var(--copper), var(--brass));
  }
  .art-bullet {
    position: absolute; left: 170px; top: 296px; width: 190px; height: 66px;
    background: linear-gradient(180deg, #d6d9dc, var(--steel));
  }
  .spec-label {
    position: absolute; right: 20px; bottom: 34px; width: 240px; height: 130px;
    background: var(--label-bg); border: 4px solid var(--navy); border-radius: 26px;
    display: flex; flex-direction: column; align-items: flex-end; justify-content: center;
    padding-right: 22px; font-family: "Rubik", sans-serif; font-weight: 800; line-height: 1.1;
  }
  .spec-label .caliber { color: var(--warn-red); font-size: 34px; }
  .spec-label .count { color: var(--navy); font-size: 30px; }
</style>
</head>
<body>
<main class="dieline">

  <section class="panel panel--side panel--warnings">
    <div class="flag-backdrop" role="img" aria-label="Waving American flag artwork in blue, white and red"></div>
    <div class="copy-card">
      <h2>WARNINGS:</h2>
      <p class="keep-away">Keep out of reach of children.</p>
      <p class="rules-title">Safety rules:</p>
      <ul class="safety-rules">
        <li>Watch your muzzle. Keep gun pointed in safe direction.</li>
        <li>Wear eye and ear protection.</li>
        <li>If gun fails to fire, keep it pointed in a safe direction, then unload carefully avoiding exposure to breech.</li>
        <li>Know your target and what is beyond it.</li>
        <li>Treat every gun as if it were loaded. Don't rely on the safety.</li>
        <li>Keep barrel clear of obstructions.</li>
        <li>Never load a gun until ready to use.</li>
        <li>Only use ammunition that exactly matches markings on your gun.</li>
      </ul>
    </div>
  </section>

  <section class="panel panel--front">
    <div class="flag-backdrop" role="img" aria-label="Waving American flag artwork in blue, white and red"></div>
    <h1 class="brand-name">Liberty<br>Range<br>Ammo <span class="brand-suffix">llc.</span></h1>
    <div class="art-cartridge" role="img" aria-label="Illustration of a brass 9mm cartridge with copper bullet"></div>
    <div class="art-bullet" role="img" aria-label="Illustration of a polished steel bullet in flight"></div>
    <div class="spec-label">
      <span class="caliber">9mm</span>
      <span class="count">100pcs</span>
    </div>
  </section>

  <section class="panel panel--side panel--lead">
    <div class="flag-backdrop" role="img" aria-label="Waving American flag artwork in red and white stripes"></div>
    <div class="copy-card lead-copy">
      <p><strong>Lead warning:</strong> This product contains lead, a substance deemed hazardous to your health. A substance that has shown to be detrimental in birth defects, reproductive harm and other ailments causing serious physical harm. Use only in well ventilated areas.</p>
      <p>Wash hands immediately and thoroughly after use.</p>
      <p>Discharging firearms in poorly-ventilated areas, cleaning firearms or handling ammunition may result in exposure to lead and other substances known to cause birth defects, reproductive harm, cancer and other serious physical injury. Have adequate ventilation at all times. Wash hands after exposure.</p>
    </div>
  </section>

</main>
</body>
</html>
```